Business Card Design & Gift cards, Gift Cert, Donation Card

Retail Gift Store-in addition to Business Cards we'd like sequenced 2 sided Gift cards, Gift Certificate Cards, and Donation Cards.please see examples and email for clarificationlogos attached with examples-
Gift Card, Gift Certificate and Donation Card will all be same style just differant upper right title, with back side info as example.
business card, as example is single sided.
looking for additional ideas for layout

Industry/Entity Type

Business

Contact Information for Business Card

211 Newman St.East Tawas, MI 48730989.362.8730Office@BrewKrew.com

Requirements
Must have
• Blue as per example
• Logos provided
• like gradiant background

```html
<!DOCTYPE html>
<html lang="en">
<head>
<meta charset="utf-8">
<title>Tillow Marsh – Business Card &amp; Gift Certificate</title>
<link rel="stylesheet" href="https://fonts.googleapis.com/css2?family=Kalam:wght@400;700&display=swap">
<style>
  :root {
    --page-bg: #a9a9a9;
    --card-border: #0b2ed8;
    --sky-top: #78b6f6;
    --sky-bottom: #c2e3f4;
    --ink: #111;
    --brand-blue: #1d34c9;
    --rule: #444;
    --mark-red: #d9231a;
    --mark-sun: #f1df1a;
    --shadow: rgba(0,0,0,0.45);
  }
  * { box-sizing: border-box; margin: 0; padding: 0; }
  html, body {
    width: 992px; height: 1200px; overflow: hidden;
    background: var(--page-bg);
    font-family: "Kalam", cursive;
    color: var(--ink);
  }
  .canvas { position: relative; width: 992px; height: 1200px; }

  .card {
    position: absolute; left: 98px; width: 808px; height: 462px;
    background: linear-gradient(180deg, var(--sky-top), var(--sky-bottom));
    box-shadow: 4px 6px 10px var(--shadow);
    overflow: hidden;
  }
  .business-card { top: 103px; border: 15px solid var(--card-border); }
  .gift-certificate { top: 623px; }

  /* Business card */
  .brand-mark {
    position: absolute; left: 17px; top: 55px; width: 260px; height: 290px;
    background: linear-gradient(160deg, var(--mark-red) 0 55%, var(--mark-sun) 55% 80%, var(--sky-bottom) 80%);
    border-radius: 6px;
  }
  .brand-name {
    position: absolute; right: 30px; top: 52px;
    font-size: 62px; font-weight: 400; line-height: 1;
    color: var(--brand-blue); letter-spacing: 0;
    white-space: nowrap;
  }
  .contact {
    position: absolute; right: 29px; top: 178px;
    text-align: right; font-size: 26px; line-height: 33px; letter-spacing: 1px;
    font-style: normal;
  }
  .services {
    position: absolute; right: 29px; top: 337px;
    text-align: right; font-size: 21px; line-height: 30px; letter-spacing: 1px;
    white-space: nowrap;
  }

  /* Gift certificate */
  .faint-mark {
    position: absolute; left: 12px; top: 18px; width: 410px; height: 430px;
    background: linear-gradient(160deg, rgba(217,35,26,0.22) 0 60%, rgba(241,223,26,0.2) 60%);
    border-radius: 8px;
  }
  .certificate-title {
    position: absolute; left: 227px; top: 88px;
    font-size: 42px; font-weight: 700; font-style: italic;
    color: var(--brand-blue); letter-spacing: 3px; line-height: 1;
    white-space: nowrap;
  }
  .fields { position: absolute; left: 247px; top: 178px; width: 454px; }
  .field {
    display: flex; align-items: flex-end; height: 48px;
    font-size: 26px; letter-spacing: 1px; line-height: 1;
  }
  .field-line { flex: 1; border-bottom: 1px solid var(--rule); margin-left: 12px; margin-bottom: 4px; }
  .record-row {
    position: absolute; left: 40px; top: 400px; width: 730px;
    display: flex; align-items: flex-end;
    font-size: 25px; letter-spacing: 0.5px; line-height: 1;
    white-space: nowrap;
  }
  .record-row .field-line { margin: 0 12px 4px 2px; }
  .record-row .number-line { flex: 0 0 117px; }
  .record-row .expiry-line { flex: 0 0 119px; margin-left: 8px; margin-right: 14px; }
  .record-row .emp-line { flex: 1 1 auto; margin-left: 8px; margin-right: 0; }
</style>
</head>
<body>
<main class="canvas">
  <section class="card business-card" aria-label="Business card">
    <div class="brand-mark" role="img" aria-label="Brand illustration: dancing figure above a rising sun"></div>
    <h1 class="brand-name">TILLOW MARSH</h1>
    <address class="contact">
      989·517·4296<br>
      Office@TillowMarsh·com<br>
      482 Larkfield Ave.<br>
      Harlow Bay, MI 48791
    </address>
    <p class="services">
      Gourmet Food, Fine Wines, Gift Baskets<br>
      Kitchen &amp; Bath Accessories, Candles, Cards, Soaps
    </p>
  </section>

  <section class="card gift-certificate" aria-label="Gift certificate">
    <div class="faint-mark" role="img" aria-label="Faint brand illustration in the background"></div>
    <h2 class="certificate-title">GIFT CERTIFICATE</h2>
    <div class="fields">
      <div class="field"><span>TO:</span><span class="field-line"></span></div>
      <div class="field"><span>FROM:</span><span class="field-line"></span></div>
      <div class="field"><span>AMOUNT:</span><span class="field-line"></span></div>
    </div>
    <div class="record-row">
      <span>NUMBER</span><span class="field-line number-line"></span>
      <span>EXPIRATION</span><span class="field-line expiry-line"></span>
      <span>EMP</span><span class="field-line emp-line"></span>
    </div>
  </section>
</main>
</body>
</html>
```